Catalogue Design Project

We need a catalog design for a new private university called Redwell Institute Bayshore (see website www.rwi-bs.org). The catalog should be about 30 pages maximum and will include items such as General Information, Academic schedule, department descriptions, program descriptions, course descriptions, school policies, student services, admissions, Bayshore Lifestyle, etc.
I will provide the text but I need a professional design with regard to page layouts. I have provided some examples.
Ok, i posted the catalog content, just missing course descriptions.
Target Market(s)
Young Professionals, Foreign Students
Industry/Entity Type
University
Look and feel
Each slider illustrates characteristics of the customer's brand and the style your logo design should communicate.

```html
<!DOCTYPE html>
<html lang="en">
<head>
<meta charset="utf-8">
<title>Redwell Institute Bayshore – General Information</title>
<link rel="stylesheet" href="https://fonts.googleapis.com/css2?family=Carlito:wght@400;700&family=Arimo:wght@700&display=swap">
<style>
  :root {
    --brand-blue: #1f5f99;
    --rule-blue: #7f9cc0;
    --ink: #1a1a1a;
    --footer-grey: #8a8a8a;
    --paper: #ffffff;
    --photo-lawn-a: #5e7a45;
    --photo-lawn-b: #3f5a30;
    --photo-study-a: #b99c80;
    --photo-study-b: #8a6a55;
    --photo-grad-a: #2b3c63;
    --photo-grad-b: #6a7fa3;
  }
  * { margin: 0; padding: 0; box-sizing: border-box; }
  html, body { width: 927px; height: 1200px; overflow: hidden; background: var(--paper); }
  .page { position: relative; width: 927px; height: 1200px; background: var(--paper); color: var(--ink); font-family: "Carlito", "Calibri", sans-serif; }

  .photo-strip { position: absolute; top: 0; left: 0; width: 927px; height: 194px; }
  .photo { position: absolute; top: 0; height: 193px; }
  .photo--lawn { left: 0; width: 391px; background: linear-gradient(180deg, #38402f 0%, var(--photo-lawn-a) 45%, var(--photo-lawn-b) 100%); }
  .photo--students { left: 395px; width: 234px; top: 33px; height: 160px; background: linear-gradient(160deg, var(--photo-study-a), var(--photo-study-b)); }
  .photo--graduate { left: 635px; width: 292px; top: 33px; height: 160px; background: linear-gradient(160deg, var(--photo-grad-a), var(--photo-grad-b)); }
  .strip-rule { position: absolute; left: 391px; top: 32px; width: 536px; height: 1px; background: var(--rule-blue); }

  .section-ribbon { position: absolute; top: 193px; left: 0; width: 927px; height: 38px; }
  .ribbon-label { position: absolute; top: 196px; left: 330px; width: 325px; text-align: center; color: #fff; font-size: 25px; letter-spacing: 0.2px; line-height: 32px; }

  .heading { position: absolute; left: 0; width: 927px; text-align: center; font-family: "Arimo", "Arial", sans-serif; font-weight: 700; font-size: 26px; line-height: 30px; }
  .body-text { position: absolute; left: 56px; width: 835px; font-size: 19.2px; line-height: 25.2px; text-align: justify; }
  .body-text p + p { text-indent: 70px; }

  .facilities-heading { top: 266px; }
  .facilities-text { top: 318px; }
  .staff-heading { top: 612px; }
  .staff-text { top: 658px; }
  .library-heading { top: 790px; }
  .library-text { top: 837px; }

  .footer-rule { position: absolute; left: 0; top: 1161px; width: 927px; height: 1px; background: var(--rule-blue); }
  .footer-folio { position: absolute; right: 40px; top: 1172px; font-size: 13px; color: var(--footer-grey); letter-spacing: 0.3px; }
</style>
</head>
<body>
<div class="page">
  <div class="photo-strip">
    <div class="photo photo--lawn" role="img" aria-label="Students relaxing on a campus lawn under trees"></div>
    <div class="strip-rule"></div>
    <div class="photo photo--students" role="img" aria-label="Group of smiling students with books in a library"></div>
    <div class="photo photo--graduate" role="img" aria-label="Graduate in cap and gown beside a waterway"></div>
  </div>

  <svg class="section-ribbon" viewBox="0 0 927 38" aria-hidden="true">
    <rect x="0" y="0" width="927" height="2" fill="var(--rule-blue)"/>
    <polygon points="330,0 655,0 641,38 344,38" fill="var(--brand-blue)"/>
  </svg>
  <div class="ribbon-label">GENERAL INFORMATION</div>

  <h2 class="heading facilities-heading">FACILITIES</h2>
  <div class="body-text facilities-text">
    <p>Redwell Institute is located at 418 Harbor Lane, in the heart of downtown Bayshore's financial district.&nbsp; Our headquarters and classrooms have been completed renovated and we are proud to have one of the most professional and modern-looking campuses in Bayshore.&nbsp; Security is also a major part of RWIB's campus plan; security cameras monitor common areas and students must have a valid ID card to enter the facility.</p>
    <p>In addition to providing students with free high-speed Wi-Fi, high-tech classrooms, traditional business classrooms, a computer lab and free beverages, the building currently hosts a restaurant, executives suites, and a fitness club.&nbsp;&nbsp; Minutes away from the Harbor Line Trolley, Coastline bus stops and major freeways, RWIB is frequently located for all visitors and means of transportation.</p>
  </div>

  <h2 class="heading staff-heading">STAFF</h2>
  <div class="body-text staff-text">
    <p>Our information desk is available during normal business hours 9:00am to 10:00pm to help students with any questions that may need including but not limited to admissions and requirements, class registration, directions to and from campus, and general information about the university and faculty.</p>
  </div>

  <h2 class="heading library-heading">LIBRARY</h2>
  <div class="body-text library-text">
    <p style="text-align:left">Students at Redwell Institute have the advantage of utilizing both the nearby Bayshore Central Library and our online services.&nbsp; We currently partner with an online library that allows students to search through thousands of articles and research materials for their courses that they wouldn't otherwise have access to.&nbsp; Students can also purchase BSU and CTU library cards and be reimbursed.</p>
  </div>

  <div class="footer-rule"></div>
  <div class="footer-folio">3::: REDWELL INSTITUTE</div>
</div>
</body>
</html>
```